Website for "Bright Morrow Ltd" cleaning bsuiness

We require a website to expose our business to the local market. We want to provide background on who we are and what we do but in an easily digestible way. We clean domestic and commercial premises and want to provide a list of all of our services to potential customers. We operate out of Warrington in the UK.

We would like the website to be animated in some way so that the experience of using it is not dull or mundane. This website needs to be an extension of our company.

Target Market(s)

30 - 60 year olds for Domestic plus commercial clients

Industry/Entity Type

Cleaning Service

Coding

Coded - Design and coding required

Number of Pages Required

4 page

Font styles to use
Sans Serif

Colors
0455a3
3176b5
85acd3
cfdeed
ffffff
000000
1b1b1b
c8c8c8
757575

Requirements
Must have
• Logo which has been provided. Theme based around the logo and its colours. Simple layout to avoid confusion.
Nice to have
• Animations where possible to impress the customer.
Should not have
• any pictures of cleaning equipment, fairies, maids etc

```html
<!DOCTYPE html>
<html lang="en">
<head>
<meta charset="utf-8">
<title>Bright Morrow Ltd – Professional Cleaning Services</title>
<link rel="stylesheet" href="https://fonts.googleapis.com/css2?family=Raleway:wght@300;400;500&family=Open+Sans:wght@400;600&family=Dancing+Script:wght@600&display=swap">
<style>
:root{
  --brand:#0455a3;
  --brand-mid:#3176b5;
  --brand-soft:#85acd3;
  --brand-pale:#cfdeed;
  --white:#ffffff;
  --ink:#1b1b1b;
  --line:#c8c8c8;
  --muted:#757575;
  --header-bg:#e6e4e1;
}
*{margin:0;padding:0;box-sizing:border-box}
html,body{width:1200px;height:2932px;overflow:hidden}
body{font-family:"Open Sans",Arial,sans-serif;color:var(--ink);background:var(--white);position:relative}
.abs{position:absolute}

/* Header */
.site-header{left:0;top:0;width:1200px;height:141px;background:linear-gradient(90deg,#e9e7e4,#dfdcd8 50%,#e9e7e4);border-bottom:4px solid var(--brand)}
.brand{left:78px;top:30px;display:flex;align-items:center;gap:14px}
.brand-mark{width:40px;height:40px;border-radius:50%;background:var(--brand)}
.brand-name{font-family:"Raleway",sans-serif;font-weight:500;font-size:36px;color:var(--brand);line-height:1}
.call{right:78px;top:20px;display:flex;align-items:center;gap:14px}
.call-label{font-family:"Dancing Script",cursive;font-size:26px;color:#333}
.call-icon{width:54px;height:54px;border-radius:50%;border:2px solid var(--brand);display:flex;align-items:center;justify-content:center}
.call-number{font-size:25px;color:var(--ink)}
.main-nav{right:56px;top:78px;display:flex;gap:6px}
.main-nav a{font-size:17px;color:var(--ink);text-decoration:none;padding:13px 22px;border-radius:24px;line-height:1}
.main-nav a.active{background:var(--brand-mid);color:var(--white)}

/* Hero */
.hero{left:0;top:145px;width:1200px;height:529px}
.hero-photo{width:100%;height:100%;background:linear-gradient(160deg,#d9dde2 0%,#eef0f2 35%,#c8c4bd 70%,#9c9891 100%)}
.hero-badge{left:94px;top:262px;width:332px;height:332px;border-radius:50%;background:rgba(49,118,181,.82);border:3px solid rgba(255,255,255,.8);text-align:center;color:var(--white)}
.hero-badge h1{font-family:"Raleway",sans-serif;font-weight:400;font-size:38px;margin-top:100px}
.hero-badge p{font-family:"Dancing Script",cursive;font-size:26px;color:var(--ink);margin-top:4px}
.btn-white{display:inline-block;margin-top:20px;background:var(--white);color:var(--brand);font-size:20px;padding:16px 26px;border-radius:28px;line-height:1}

/* Blue bands */
.band{left:0;width:1200px;background:radial-gradient(ellipse at 30% 40%,#0b60ae,var(--brand) 60%);color:var(--white);text-align:center}
.band h2{font-family:"Raleway",sans-serif;font-weight:400;font-size:40px;letter-spacing:.5px}
.band p{font-size:13.5px;line-height:27px;color:#dfe9f4;width:900px;margin:0 auto}
.welcome{top:674px;height:313px}
.welcome h2{margin-top:54px}
.welcome p{margin-top:12px}
.btn-soft{display:inline-block;margin-top:22px;background:var(--brand-mid);color:var(--white);font-size:20px;padding:17px 29px;border-radius:28px;line-height:1}

/* Services */
.services{left:0;top:987px;width:1200px;height:844px;background:var(--brand-pale)}
.section-title{font-family:"Raleway",sans-serif;font-weight:400;font-size:40px;color:var(--brand);text-align:center}
.services .section-title{margin-top:50px}
.group-title{left:78px;font-family:"Raleway",sans-serif;font-size:24px;color:var(--brand)}
.group-sub{left:78px;font-family:"Dancing Script",cursive;font-size:20px;color:var(--ink)}
.arrows{right:78px;display:flex;gap:6px}
.cards{left:78px;display:flex;gap:0}
.card{position:absolute;height:222px;border:5px solid var(--brand);background:var(--brand-mid)}
.card-photo{height:166px;background:linear-gradient(160deg,#ece9e4,#a88f78)}
.card-label{height:46px;display:flex;align-items:center;justify-content:center;color:var(--white);font-size:20px}

/* Testimonial */
.testimonial{top:1831px;height:416px}
.testimonial h2{margin-top:56px}
.avatar{width:114px;height:114px;border-radius:50%;border:4px solid var(--white);background:linear-gradient(180deg,#f1e2c6,#d9b99a);margin:22px auto 16px}
.client{font-weight:600;font-size:16px;margin-top:12px}

/* Contact */
.contact{left:0;top:2247px;width:1200px;height:469px;background:var(--brand-pale);text-align:center}
.contact .section-title{margin-top:50px}
.contact-intro{font-size:13.5px;line-height:26px;color:#333;width:760px;margin:10px auto 0}
.field{position:absolute;background:var(--white);border:1px solid var(--line);font-size:13px;color:var(--muted);text-align:left;padding:12px 14px}
.btn-submit{left:518px;top:350px;width:164px;height:55px;border-radius:28px;background:var(--brand-mid);color:var(--white);font-size:20px;line-height:55px}

/* Footer */
.site-footer{left:0;top:2716px;width:1200px;height:216px;background:var(--brand);color:var(--white)}
.foot-nav{left:78px;top:30px;display:flex;gap:4px}
.foot-nav a{font-size:14px;color:var(--white);text-decoration:none;padding:14px 18px;border-radius:24px;line-height:1}
.foot-nav a.active{background:var(--brand-mid);padding:14px 26px}
.socials{right:78px;top:24px;display:flex;gap:10px}
.social{width:46px;height:46px;border-radius:50%;border:2px solid var(--brand-soft);display:flex;align-items:center;justify-content:center}
.social span{width:14px;height:14px;border-radius:50%;background:var(--white)}
.foot-rule{left:78px;top:92px;width:1044px;height:1px;background:rgba(255,255,255,.25)}
.foot-heading{left:80px;top:106px;font-size:17px;font-weight:600}
.foot-item{top:142px;display:flex;align-items:center;gap:18px;font-size:14px;line-height:24px}
.foot-icon{width:50px;height:50px;border-radius:50%;display:flex;align-items:center;justify-content:center;flex:none}
.foot-icon.fill{background:var(--brand-mid)}
.foot-icon.ring{border:2px solid var(--brand-soft)}
</style>
</head>
<body>

<header class="site-header abs">
  <div class="brand abs"><span class="brand-mark"></span><span class="brand-name">Bright Morrow</span></div>
  <div class="call abs">
    <span class="call-label">Call Us On :</span>
    <span class="call-icon"><svg width="26" height="26" viewBox="0 0 24 24"><path d="M6.6 10.8a15 15 0 0 0 6.6 6.6l2.2-2.2c.3-.3.7-.4 1-.2 1.1.4 2.3.6 3.6.6.6 0 1 .4 1 1V20c0 .6-.4 1-1 1A17 17 0 0 1 3 4c0-.6.4-1 1-1h3.5c.6 0 1 .4 1 1 0 1.3.2 2.5.6 3.6.1.3 0 .7-.2 1z" fill="#0455a3"/></svg></span>
    <span class="call-number">555 012 3468</span>
  </div>
  <nav class="main-nav abs">
    <a class="active" href="#">HOME</a><a href="#">ABOUT US</a><a href="#">SERVICES</a><a href="#">BLOG</a><a href="#">CONTACT US</a>
  </nav>
</header>

<section class="hero abs">
  <div class="hero-photo" role="img" aria-label="Bright, clean living room with white furniture, grey sofa and wooden floor"></div>
</section>
<div class="hero-badge abs">
  <h1>Bright Morrow</h1>
  <p>Professional Cleaning Services</p>
  <span class="btn-white">CONTACT US</span>
</div>

<section class="band welcome abs">
  <h2>WELCOME TO BRIGHT MORROW</h2>
  <p>Lorem Ipsum is simply dummy text of the printing and typesetting industry. Lorem Ipsum has been the industry's standard dummy text ever since the 1500s, when an unknown printer took a galley of type and scrambled it to make a type specimen book.It has survived not only five centuries. Lorem Ipsum is simply dummy text of the printing and typesetting industry.</p>
  <span class="btn-soft">KNOW MORE</span>
</section>

<section class="services abs">
  <h2 class="section-title">OUR SERVICES</h2>

  <div class="group-title abs" style="top:134px">DOMESTIC SERVICES :</div>
  <div class="group-sub abs" style="top:168px">Weekly, fortnightly, monthly and adhoc cleans available</div>
  <div class="arrows abs" style="top:138px"><svg width="44" height="24" viewBox="0 0 44 24"><path d="M16 3 6 12l10 9M28 3l10 9-10 9" stroke="#0455a3" stroke-width="2.5" fill="none"/></svg></div>

  <div class="card" style="left:78px;top:213px;width:246px"><div class="card-photo" role="img" aria-label="Carpet cleaning in a living room"></div><div class="card-label">Carpet Cleaning</div></div>
  <div class="card" style="left:344px;top:213px;width:248px"><div class="card-photo" style="background:linear-gradient(160deg,#f2f4f7,#a9b7c8)" role="img" aria-label="Folded laundry beside an iron"></div><div class="card-label">Ironing</div></div>
  <div class="card" style="left:608px;top:213px;width:248px"><div class="card-photo" style="background:linear-gradient(160deg,#e6edf3,#8fa3b6)" role="img" aria-label="Tiled floor being steam cleaned"></div><div class="card-label">Tiled floor steam clean</div></div>
  <div class="card" style="left:872px;top:213px;width:250px"><div class="card-photo" style="background:linear-gradient(160deg,#f3ebe0,#c49a6c)" role="img" aria-label="Empty room with moving boxes"></div><div class="card-label">End of tenancy clean</div></div>

  <div class="group-title abs" style="top:479px">COMMERCIAL CLEANING :</div>
  <div class="group-sub abs" style="top:513px">Weekly, fortnightly, monthly and adhoc cleans available</div>
  <div class="arrows abs" style="top:483px"><svg width="44" height="24" viewBox="0 0 44 24"><path d="M16 3 6 12l10 9M28 3l10 9-10 9" stroke="#0455a3" stroke-width="2.5" fill="none"/></svg></div>

  <div class="card" style="left:78px;top:556px;width:250px"><div class="card-photo" style="background:linear-gradient(160deg,#f0efed,#7d6450)" role="img" aria-label="Office floor being vacuumed"></div><div class="card-label">Vacuuming</div></div>
  <div class="card" style="left:344px;top:556px;width:248px"><div class="card-photo" style="background:linear-gradient(160deg,#e9ddd1,#9b5a2c)" role="img" aria-label="Wooden desk being polished"></div><div class="card-label">Desk polishing</div></div>
  <div class="card" style="left:604px;top:556px;width:250px"><div class="card-photo" style="background:linear-gradient(160deg,#5d7c3e,#8a8f8c)" role="img" aria-label="Commercial waste bins outdoors"></div><div class="card-label">Bin emptying</div></div>
  <div class="card" style="left:872px;top:556px;width:250px"><div class="card-photo" style="background:linear-gradient(160deg,#f4f4f4,#b9bcc0)" role="img" aria-label="Clean white washroom"></div><div class="card-label">Toilet cleaning</div></div>
</section>

<section class="band testimonial abs">
  <h2>WHAT OUR CLIENT SAY</h2>
  <div class="avatar" role="img" aria-label="Client portrait"></div>
  <p>Lorem Ipsum is simply dummy text of the printing and typesetting industry. Lorem Ipsum has been the industry's standard dummy text ever since the 1500s, when an unknown printer took a galley &nbsp;tmake a type specimen book.</p>
  <p class="client">- CLIENT NAME</p>
</section>

<section class="contact abs">
  <h2 class="section-title">CONTACT US</h2>
  <p class="contact-intro">Lorem Ipsum is simply dummy text of the printing and typesetting industry. Lorem Ipsum has been the industry's standard dummy text ever since the when an unknown printer took a galley.</p>
  <div class="field" style="left:201px;top:172px;width:260px;height:49px">Name*</div>
  <div class="field" style="left:469px;top:172px;width:260px;height:49px">Email*</div>
  <div class="field" style="left:737px;top:172px;width:262px;height:49px">Phone*</div>
  <div class="field" style="left:201px;top:229px;width:798px;height:113px">Message*</div>
  <div class="btn-submit abs">SUBMIT</div>
</section>

<footer class="site-footer abs">
  <nav class="foot-nav abs"><a class="active" href="#">Home</a><a href="#">About Us</a><a href="#">Services</a><a href="#">Blog</a><a href="#">Contact Us</a></nav>
  <div class="socials abs"><span class="social"><span></span></span><span class="social"><span></span></span><span class="social"><span></span></span></div>
  <div class="foot-rule abs"></div>
  <div class="foot-heading abs">GET IN TOCH</div>
  <div class="foot-item abs" style="left:78px;width:260px">
    <span class="foot-icon fill"><svg width="20" height="26" viewBox="0 0 20 26"><path d="M10 0a10 10 0 0 0-10 10c0 7 10 16 10 16s10-9 10-16A10 10 0 0 0 10 0zm0 14a4 4 0 1 1 0-8 4 4 0 0 1 0 8z" fill="#fff"/></svg></span>
    <span>101 - Lorem ipsum is the<br>simple dummy text.</span>
  </div>
  <div class="foot-item abs" style="left:344px">
    <span class="foot-icon ring"><svg width="22" height="22" viewBox="0 0 24 24"><path d="M6.6 10.8a15 15 0 0 0 6.6 6.6l2.2-2.2c.3-.3.7-.4 1-.2 1.1.4 2.3.6 3.6.6.6 0 1 .4 1 1V20c0 .6-.4 1-1 1A17 17 0 0 1 3 4c0-.6.4-1 1-1h3.5c.6 0 1 .4 1 1 0 1.3.2 2.5.6 3.6.1.3 0 .7-.2 1z" fill="#fff"/></svg></span>
    <span>555 012 3468</span>
  </div>
  <div class="foot-item abs" style="left:606px">
    <span class="foot-icon fill"><svg width="24" height="18" viewBox="0 0 24 18"><rect x="1" y="1" width="22" height="16" rx="2" fill="none" stroke="#fff" stroke-width="2"/><path d="m1 2 11 8 11-8" fill="none" stroke="#fff" stroke-width="2"/></svg></span>
    <span>info@brightmorrow.example</span>
  </div>
  <div class="foot-item abs" style="left:876px;width:250px">
    <span>© 2016 <strong>Bright Morrow</strong> - &nbsp;All<br>rights reserved.</span>
  </div>
</footer>

</body>
</html>
```